A website for Kovadrel Limited

We need a new and modern website for our company. We are engineering consultants and contractors (EPC) in the oil and gas industry and building services industry.
What we do:
Engineering, procurement, construction
Automation (safety and process)
Non-destructive testing
Training
We have an existing website and the content can be referred from there since we are remaking the website
For more information visit Kovadrel Limited Kenya

```html
<!DOCTYPE html>
<html lang="en">
<head>
<meta charset="utf-8">
<title>Kovadrel Limited</title>
<link href="https://fonts.googleapis.com/css2?family=Cinzel:wght@600;700&family=Poppins:ital,wght@0,400;0,500;0,600;1,400&display=swap" rel="stylesheet">
<style>
:root{
  --orange:#ee7d33;
  --orange-light:#f6b46a;
  --orange-deep:#e2652a;
  --ink:#1c1c1c;
  --body:#3f3f3f;
  --muted:#8a8a8a;
  --grey-bg:#ededed;
  --line:#dcdcdc;
  --white:#ffffff;
}
*{box-sizing:border-box;margin:0;padding:0}
html,body{width:1200px;height:5204px;overflow:hidden;background:var(--white)}
body{position:relative;font-family:"Poppins",sans-serif;color:var(--body)}
.abs{position:absolute}
.display{font-family:"Cinzel",serif;font-weight:700;color:var(--ink);letter-spacing:1px}
.section-title{position:absolute;left:0;width:1200px;text-align:center;font-size:44px}
.rule{position:absolute;left:561px;width:78px;height:5px;background:var(--orange)}
.btn{position:absolute;background:var(--orange);color:var(--white);font-size:13px;font-weight:600;text-transform:uppercase;display:flex;align-items:center;justify-content:center;letter-spacing:.5px}
.btn::after{content:"";position:absolute;left:6px;top:6px;right:-6px;bottom:-6px;border:2px solid var(--orange);border-left:none;border-top:none}

/* header */
.brand{display:flex;align-items:center;gap:8px}
.brand-mark{width:74px;height:74px;border-radius:50%;background:var(--orange)}
.brand-name{font-family:"Cinzel",serif;font-weight:600;font-size:23px;line-height:29px;color:#555}
.contact-chip{display:flex;align-items:center;gap:8px;font-size:12px;line-height:16px;color:#444}
.chip-icon{width:32px;height:32px;border-radius:50%;background:var(--orange);display:flex;align-items:center;justify-content:center}
.nav{top:107px;left:0;width:1200px;height:53px;background:#0c0c0c;display:flex;padding-left:130px}
.nav a{color:var(--white);text-decoration:none;font-size:13px;font-weight:500;padding:0 17px;display:flex;align-items:center;text-transform:uppercase}
.nav a.active{background:var(--orange);padding:0 20px}

/* hero */
.hero{top:160px;left:0;width:1200px;height:640px;background:linear-gradient(180deg,#4a5670 0%,#6b5a56 35%,#8e6a44 60%,#3a3028 100%)}
.hero-title{top:345px;width:1200px;text-align:center;font-size:56px;color:var(--white)}
.hero-sub{top:425px;width:1200px;text-align:center;font-family:"Cinzel",serif;font-size:20px;color:#f1f1f1}

/* who */
.who-photo{top:800px;left:740px;width:460px;height:560px;background:linear-gradient(100deg,#ffffff 0%,#d9d9d9 35%,#b6aba2 60%,#e8a25a 78%,#9a8f88 100%)}
.who-text{font-size:14.5px;line-height:24px;color:var(--body);width:450px}

/* services */
.service{position:absolute;top:1580px;height:230px;border:2px solid #f0a66f;border-radius:10px;text-align:center}
.service .icon{width:70px;height:76px;margin:38px auto 16px;background:linear-gradient(180deg,#fbd4b0,#f29a54);border-radius:6px}
.service .name{font-size:12px;line-height:15px;color:#333;text-transform:uppercase;height:34px}
.service .more{font-size:11px;font-weight:600;color:#333;text-decoration:underline;margin-top:12px;display:block}

/* products */
.product{position:absolute;top:2140px;width:213px;height:285px;background:var(--white);border:2px solid #e58b5a}
.product .photo{height:220px}
.product .label{font-size:17px;font-weight:600;color:var(--ink);text-align:center;line-height:62px;text-transform:uppercase}

/* projects */
.project{position:absolute;top:2762px;width:294px;height:318px;background:var(--white);box-shadow:0 2px 10px rgba(0,0,0,.12)}
.project .photo{height:202px}
.project h3{font-size:14px;font-weight:600;color:var(--ink);line-height:18px;margin:26px 28px 10px;text-transform:uppercase}
.project p{font-size:11.5px;line-height:15px;color:var(--muted);margin:0 28px}
.project a{font-size:11.5px;font-weight:600;color:var(--orange);margin:2px 28px;display:block;text-decoration:none}

/* clients */
.quote{top:3484px;width:1200px;text-align:center;font-size:19.5px;font-style:italic;line-height:29px;color:#444}

/* partners */
.partner{position:absolute;top:4005px;height:90px;display:flex;flex-direction:column;align-items:center;gap:10px}
.partner .shape{width:66px;height:62px;border-radius:50%;background:#3b3b3b}
.partner .bar{width:120px;height:12px;background:#3b3b3b;border-radius:2px}

/* quote form */
.field{position:absolute;background:var(--white);font-size:12px;color:#777;padding:10px 12px}

/* footer */
.foot-head{font-size:15px;font-weight:600;color:#222;text-transform:uppercase}
.foot-links{list-style:none;font-size:13px;line-height:25px;color:#444}
.foot-contact{display:flex;gap:14px;font-size:13px;line-height:20px;color:#444}
</style>
</head>
<body>

<!-- header -->
<header>
  <div class="abs brand" style="top:14px;left:150px">
    <div class="brand-mark"></div>
    <div class="brand-name">Kovadrel<br>Limited</div>
  </div>
  <div class="abs contact-chip" style="top:35px;left:530px">
    <div class="chip-icon"><svg width="16" height="12" viewBox="0 0 16 12"><rect x="1" y="1" width="14" height="10" fill="none" stroke="#fff" stroke-width="1.6"/><path d="M1 1l7 6 7-6" fill="none" stroke="#fff" stroke-width="1.6"/></svg></div>
    <div>EMAIL US:<br>INFO@KOVADREL.CO.KE</div>
  </div>
  <div class="abs contact-chip" style="top:35px;left:773px">
    <div class="chip-icon"><svg width="16" height="16" viewBox="0 0 24 24"><path d="M6.6 10.8a15 15 0 006.6 6.6l2.2-2.2c.3-.3.7-.4 1-.2 1.1.4 2.3.6 3.6.6.6 0 1 .4 1 1V20c0 .6-.4 1-1 1A17 17 0 013 4c0-.6.4-1 1-1h3.5c.6 0 1 .4 1 1 0 1.3.2 2.5.6 3.6.1.3 0 .7-.2 1z" fill="#fff"/></svg></div>
    <div>+254 700 410 101<br>+254 700 410 202</div>
  </div>
  <div class="abs chip-icon" style="top:37px;left:1010px;width:36px;height:36px">
    <svg width="16" height="16" viewBox="0 0 16 16"><rect x="2" y="5" width="12" height="10" rx="1" fill="#fff"/><path d="M5 5V4a3 3 0 016 0v1" fill="none" stroke="#fff" stroke-width="1.6"/></svg>
  </div>
  <nav class="abs nav">
    <a class="active">Home</a><a>About Us</a><a>Services</a><a>Products</a><a>Projects</a><a>Our Clients</a><a>Our Partners</a><a>Contacts</a>
  </nav>
</header>

<!-- hero -->
<section>
  <div class="abs hero" role="img" aria-label="Oil refinery with storage tanks lit at dusk"></div>
  <h1 class="abs display hero-title">Kovadrel Limited</h1>
  <p class="abs hero-sub">We are engineering consultants and ontractors</p>
  <div class="btn" style="top:478px;left:520px;width:160px;height:42px">Learn More</div>
  <svg class="abs" style="top:740px;left:0" width="1200" height="70" viewBox="0 0 1200 70">
    <defs><linearGradient id="heroBand" x1="0" x2="1"><stop offset="0" stop-color="#e8763a"/><stop offset="1" stop-color="#f6b46a"/></linearGradient></defs>
    <polygon points="0,10 1200,40 1200,70 0,70" fill="url(#heroBand)"/>
    <polygon points="0,60 1200,25 1200,70 0,70" fill="#fff"/>
  </svg>
</section>

<!-- who we are -->
<section>
  <div class="abs who-photo" role="img" aria-label="Engineer in a hard hat blended with a refinery skyline"></div>
  <h2 class="abs display" style="top:895px;left:152px;font-size:44px">Who We Are</h2>
  <div class="abs" style="top:958px;left:153px;width:98px;height:5px;background:var(--orange)"></div>
  <p class="abs who-text" style="top:985px;left:152px">Kovadrel undertakes Design, Supply, Installation and Commissioning of LPG and Petroleum systems including LPG Reticulated Systems (piped gas). We also do LPG tank revalidation and recertification.</p>
  <p class="abs who-text" style="top:1103px;left:152px">Our clients include: Oil companies (both multinationals and local), government agencies, manufacturing companies, agricultural institutions, and the building services industry.</p>
  <div class="btn" style="top:1200px;left:153px;width:137px;height:42px">About Us</div>
</section>

<!-- services -->
<section>
  <h2 class="display section-title" style="top:1465px">Our Services</h2>
  <div class="rule" style="top:1527px"></div>
  <div class="service" style="left:72px;width:190px"><div class="icon" role="img" aria-label="Oil barrel icon"></div><div class="name"><br>EPC</div><span class="more">Read More</span></div>
  <div class="service" style="left:282px;width:190px"><div class="icon" role="img" aria-label="Pump jack icon"></div><div class="name">LPG and<br>Petroleum</div><span class="more">Read More</span></div>
  <div class="service" style="left:490px;width:222px"><div class="icon" role="img" aria-label="Engineer with gear icon"></div><div class="name">Engineering Consulting/<br>Project Management</div><span class="more">Read More</span></div>
  <div class="service" style="left:730px;width:190px"><div class="icon" role="img" aria-label="Gear and wrench icon"></div><div class="name">Non Destructive<br>Testing</div><span class="more">Read More</span></div>
  <div class="service" style="left:942px;width:190px"><div class="icon" role="img" aria-label="Trainer at a board icon"></div><div class="name"><br>Training</div><span class="more">Read More</span></div>
</section>

<!-- products -->
<section>
  <div class="abs" style="top:1925px;left:0;width:1200px;height:640px;background:linear-gradient(180deg,#f2f2f2,#e4e4e4)" role="img" aria-label="Faded oil rig landscape backdrop"></div>
  <svg class="abs" style="top:1920px;left:0" width="1200" height="650" viewBox="0 0 1200 650">
    <defs><linearGradient id="prodBand" x1="0" x2="1"><stop offset="0" stop-color="#f0873d"/><stop offset="1" stop-color="#f6b46a"/></linearGradient></defs>
    <polygon points="0,0 1200,0 1200,8 0,50" fill="#fff"/>
    <polygon points="450,32 1200,10 1200,60" fill="url(#prodBand)"/>
    <polygon points="0,595 820,640 0,650" fill="url(#prodBand)"/>
    <polygon points="0,650 1200,580 1200,650" fill="#fff"/>
  </svg>
  <h2 class="display section-title" style="top:2022px">Products</h2>
  <div class="rule" style="top:2085px"></div>
  <div class="product" style="left:124px"><div class="photo" role="img" aria-label="LPG storage tanks at a plant" style="background:linear-gradient(180deg,#6d7fae,#b9b3c2 55%,#e6e6ee)"></div><div class="label">LPG</div></div>
  <div class="product" style="left:370px"><div class="photo" role="img" aria-label="Offshore oil platform at sea" style="background:linear-gradient(180deg,#a8bccf,#6d7d88 55%,#2f3840)"></div><div class="label">Petroleum</div></div>
  <div class="product" style="left:616px"><div class="photo" role="img" aria-label="Engineer at an automation control panel" style="background:linear-gradient(160deg,#2c3d4c,#425668 50%,#c9843f)"></div><div class="label">Automation</div></div>
  <div class="product" style="left:862px"><div class="photo" role="img" aria-label="Firefighters at an industrial fire" style="background:linear-gradient(180deg,#8d9096,#b5a08a 55%,#c0392b)"></div><div class="label">Firefighting</div></div>
</section>

<!-- projects -->
<section>
  <h2 class="display section-title" style="top:2660px">Projects</h2>
  <div class="rule" style="top:2721px"></div>
  <article class="project" style="left:130px">
    <div class="photo" role="img" aria-label="Pipelines at sunset" style="background:linear-gradient(180deg,#5a4a52,#d98a4a 45%,#8a4a2e)"></div>
    <h3>Piped Gas - LPG<br>Reticulation</h3>
    <p>Lorem ipsum dolor sit amet, conse ctetur adipiscing elit, sed do eiusmod tempor incididunt ut laboreetdolo.</p><a>Read More</a>
  </article>
  <article class="project" style="left:454px">
    <div class="photo" role="img" aria-label="Petroleum depot tanks lit at night" style="background:linear-gradient(180deg,#2e3a52,#7a6452 55%,#d9944a)"></div>
    <h3>Petroleum and LPG<br>Terminals/ Depots</h3>
    <p>Lorem ipsum dolor sit amet, conse ctetur adipiscing elit, sed do eiusmod tempor incididunt ut laboreetdolo.</p><a>Read More</a>
  </article>
  <article class="project" style="left:780px">
    <div class="photo" role="img" aria-label="Fuel tanker trucks at a petrol station" style="background:linear-gradient(180deg,#6e86a8,#c6ccd4 55%,#8a8c8f)"></div>
    <h3 style="margin-top:44px">Petrol Stations</h3>
    <p>Lorem ipsum dolor sit amet, conse ctetur adipiscing elit, sed do eiusmod tempor incididunt ut laboreetdolo.</p><a>Read More</a>
  </article>
</section>

<!-- clients -->
<section>
  <svg class="abs" style="top:3235px;left:0" width="1200" height="600" viewBox="0 0 1200 600">
    <polygon points="0,0 1200,0 1200,505 0,560" fill="#ececec"/>
  </svg>
  <h2 class="display section-title" style="top:3360px">Our Clients</h2>
  <div class="rule" style="top:3421px"></div>
  <p class="abs quote">Lorem ipsum dolor sit amet, consectetur adipiscing elit, sed do eiusmod tempor<br>incididunt ut labore et dolore magna aliqua. Quis ipsum suspendisse ultrices gravida.<br>Risus commodo viverra maecenas accumsan lacus vel facilisis.</p>
  <div class="abs" role="img" aria-label="Client portrait" style="top:3596px;left:478px;width:102px;height:102px;border-radius:50%;background:linear-gradient(160deg,#e8b04a,#9a9a7a 55%,#6a7a4a)"></div>
  <div class="abs" style="top:3620px;left:592px;font-size:15px;color:#222;text-transform:uppercase">Dara Minek</div>
  <div class="abs" style="top:3646px;left:594px;font-size:12px;color:#444">Lorem Ipsum</div>
</section>

<!-- partners -->
<section>
  <h2 class="display section-title" style="top:3880px">Partners</h2>
  <div class="rule" style="top:3941px"></div>
  <div class="partner" style="left:135px;width:120px" role="img" aria-label="Partner badge"><div class="shape"></div><div class="bar"></div></div>
  <div class="partner" style="left:323px;width:120px" role="img" aria-label="Partner badge"><div class="shape"></div><div class="bar"></div></div>
  <div class="partner" style="left:512px;width:140px;justify-content:center" role="img" aria-label="Partner badge"><div class="bar" style="width:140px;height:44px;border-radius:22px"></div></div>
  <div class="partner" style="left:727px;width:130px" role="img" aria-label="Partner badge"><div class="shape" style="border-radius:8px"></div><div class="bar" style="width:130px"></div></div>
  <div class="partner" style="left:930px;width:130px" role="img" aria-label="Partner badge"><div class="shape"></div><div class="bar" style="width:130px"></div></div>
</section>

<!-- get a quote -->
<section>
  <div class="abs" role="img" aria-label="Construction workers on site with an orange tint" style="top:4170px;left:0;width:1200px;height:560px;background:linear-gradient(180deg,#f08a3c 0%,#f39a55 55%,#f6b07a 100%)"></div>
  <svg class="abs" style="top:4165px;left:0" width="1200" height="570" viewBox="0 0 1200 570">
    <polygon points="0,0 1200,0 0,20" fill="#fff"/>
    <polygon points="730,58 1200,40 1200,95" fill="#c9c9c9"/>
    <polygon points="0,505 560,480 0,560" fill="#c9c9c9"/>
    <polygon points="0,570 1200,478 1200,570" fill="#fff"/>
  </svg>
  <h2 class="abs display" style="top:4312px;width:1200px;text-align:center;font-size:36px;color:var(--white)">Get a Quote</h2>
  <div class="abs" style="top:4360px;left:561px;width:78px;height:4px;background:var(--white)"></div>
  <div class="field" style="top:4392px;left:332px;width:261px;height:40px">Name :</div>
  <div class="field" style="top:4392px;left:600px;width:286px;height:40px">Phone :</div>
  <div class="field" style="top:4443px;left:332px;width:261px;height:40px">Email :</div>
  <div class="field" style="top:4443px;left:600px;width:286px;height:40px">Subject:</div>
  <div class="field" style="top:4495px;left:332px;width:554px;height:112px">Message :</div>
  <div class="abs" style="top:4568px;left:543px;width:117px;height:38px;background:#111;color:#fff;font-size:14px;font-weight:600;display:flex;align-items:center;justify-content:center;box-shadow:4px 4px 0 #fff">SUBMIT</div>
</section>

<!-- footer -->
<footer>
  <div class="abs brand" style="top:4800px;left:152px">
    <div class="brand-mark" style="width:88px;height:88px"></div>
    <div class="brand-name" style="font-size:26px;line-height:32px">Kovadrel<br>Limited</div>
  </div>
  <p class="abs" style="top:4906px;left:150px;width:290px;font-size:13px;line-height:21px;color:#444">Kovadrel' core business is engineering works (Oil and Gas Engineering).</p>
  <div class="abs" style="top:4968px;left:154px;display:flex;gap:10px">
    <span style="width:22px;height:22px;border-radius:50%;background:var(--orange)" aria-label="Social profile"></span>
    <span style="width:22px;height:22px;border-radius:50%;background:var(--orange)" aria-label="Social profile"></span>
    <span style="width:22px;height:22px;border-radius:50%;background:var(--orange)" aria-label="Social profile"></span>
  </div>
  <div class="abs" style="top:4760px;left:470px;width:2px;height:270px;background:var(--line)"></div>
  <div class="abs" style="top:4760px;left:680px;width:2px;height:270px;background:var(--line)"></div>

  <h4 class="abs foot-head" style="top:4783px;left:520px">Menu</h4>
  <div class="abs" style="top:4810px;left:520px;width:60px;height:3px;background:var(--orange)"></div>
  <ul class="abs foot-links" style="top:4843px;left:528px">
    <li>Home</li><li>About us</li><li>Services</li><li>Products</li><li>Our Projects</li><li>Our Clients</li><li>Partners</li>
  </ul>

  <h4 class="abs foot-head" style="top:4783px;left:738px">Contact Us</h4>
  <div class="abs" style="top:4810px;left:738px;width:60px;height:3px;background:var(--orange)"></div>
  <div class="abs foot-contact" style="top:4850px;left:740px;width:340px">
    <div class="chip-icon" style="flex:none;margin-top:6px"><svg width="14" height="14" viewBox="0 0 24 24"><path d="M6.6 10.8a15 15 0 006.6 6.6l2.2-2.2c.3-.3.7-.4 1-.2 1.1.4 2.3.6 3.6.6.6 0 1 .4 1 1V20c0 .6-.4 1-1 1A17 17 0 013 4c0-.6.4-1 1-1h3.5c.6 0 1 .4 1 1 0 1.3.2 2.5.6 3.6.1.3 0 .7-.2 1z" fill="#fff"/></svg></div>
    <div>Riverbend Court, Next to Cedar Mall, Suite 14, Harbour Road<br>P.O. Box 40120-00100 Nairobi</div>
  </div>
  <div class="abs foot-contact" style="top:4935px;left:740px;align-items:center">
    <div class="chip-icon"><svg width="14" height="14" viewBox="0 0 24 24"><path d="M6.6 10.8a15 15 0 006.6 6.6l2.2-2.2c.3-.3.7-.4 1-.2 1.1.4 2.3.6 3.6.6.6 0 1 .4 1 1V20c0 .6-.4 1-1 1A17 17 0 013 4c0-.6.4-1 1-1h3.5c.6 0 1 .4 1 1 0 1.3.2 2.5.6 3.6.1.3 0 .7-.2 1z" fill="#fff"/></svg></div>
    <div>Cell: +254 700 410 303, +254 700 410 101</div>
  </div>
  <div class="abs foot-contact" style="top:4980px;left:740px;align-items:center">
    <div class="chip-icon"><svg width="14" height="11" viewBox="0 0 16 12"><rect x="1" y="1" width="14" height="10" fill="none" stroke="#fff" stroke-width="1.6"/><path d="M1 1l7 6 7-6" fill="none" stroke="#fff" stroke-width="1.6"/></svg></div>
    <div>info@kovadrel.co.ke</div>
  </div>

  <div class="abs" role="img" aria-label="Faint industrial skyline" style="top:5060px;left:0;width:1200px;height:144px;background:linear-gradient(180deg,#ffffff 0%,#e2e4e8 45%,#d3d6db 100%)"></div>
  <p class="abs" style="top:5150px;width:1200px;text-align:center;font-size:13px;color:#333">Copyrights © 2023 Kovadrel Limited. All rights Reserved</p>
</footer>

</body>
</html>
```